Kettle Ridge Kitchen Hour Podcast Episode Cover

I’m looking for a clean, professional, and eye-catching podcast episode cover template for my show, Kettle Ridge Kitchen Hour. Each week, I feature a new guest, so the design must allow me (or my team) to easily swap in a new guest’s photo without needing advanced design skills.

The template should be:

- Drag-and-drop friendly: simple for me to replace the guest’s headshot in Canva, Photoshop, or similar.
- On-brand with the Kettle Ridge Kitchen Hour podcast: professional yet approachable, foodservice industry-focused.
- Bold and attention-grabbing for podcast platforms and social media.

Readable text at small sizes, since covers are often viewed as thumbnails.

Design Elements to Include:

1. Podcast Title: “Kettle Ridge Kitchen Hour” (prominently displayed)
2. Subtitle/Space: Line for guest’s name, professional title, and company name
3. Photo Placeholder: Large, central area where I can easily drag and drop a guest photo
4. Brand Colors: attached
5. Clean, modern fonts (easy to read at thumbnail size)
6. Background graphics or patterns that give a sense of foodservice, leadership, or nationwide reach... but do not overpower the guest photo

Format Requirements:

- Editable source file (PSD, Canva template, or layered AI/INDD)
- JPG/PNG exports for immediate use
- Square format (3000x3000px) for podcast platforms

Style Inspiration:
Think modern podcast covers: bold fonts, clean lines, professional with a touch of energy.

Deliverables:

1. Final episode cover template (editable file)
2. Instructions or guidance on how to swap out guest photos

```html
<!DOCTYPE html>
<html lang="en">
<head>
<meta charset="utf-8">
<title>Kettle Ridge Kitchen Hour – Episode Cover</title>
<link href="https://fonts.googleapis.com/css2?family=Bebas+Neue&family=Poppins:wght@400;500;700&family=Yellowtail&display=swap" rel="stylesheet">
<style>
  :root {
    --navy: #1b3850;
    --navy-ring: #22455c;
    --grid: rgba(10, 30, 45, 0.45);
    --gold: #f4b41a;
    --white: #ffffff;
    --placeholder-a: #d9d9d9;
    --placeholder-b: #c9c9c9;
    --prop-dark: #2a2d31;
    --prop-mid: #5a5f66;
  }
  * { box-sizing: border-box; margin: 0; padding: 0; }
  html, body { width: 1200px; height: 1200px; overflow: hidden; background: var(--navy); }
  .cover {
    position: relative;
    width: 1200px;
    height: 1200px;
    background: var(--navy);
    overflow: hidden;
    font-family: "Poppins", sans-serif;
    color: var(--white);
  }
  .backdrop { position: absolute; inset: 0; }
  .show-title {
    position: absolute;
    left: 0; right: 0;
    text-align: center;
    font-family: "Bebas Neue", sans-serif;
    line-height: 1;
    letter-spacing: 1px;
  }
  .show-title--top { top: 82px; font-size: 196px; color: var(--white); }
  .show-title--bottom { top: 268px; font-size: 196px; color: var(--gold); }
  .photo-frame {
    position: absolute;
    left: 211px; top: 460px;
    width: 778px; height: 401px;
    border: 2px solid var(--gold);
    border-radius: 62px;
  }
  .guest-photo {
    position: absolute;
    left: 243px; top: 491px;
    width: 713px; height: 338px;
    border-radius: 40px;
    background: linear-gradient(135deg, var(--placeholder-a), var(--placeholder-b));
  }
  .prop {
    position: absolute;
    background: linear-gradient(150deg, var(--prop-mid), var(--prop-dark));
    opacity: 0.85;
  }
  .prop--headphones-top { left: 1040px; top: 24px; width: 160px; height: 200px; border-radius: 80px 0 0 80px; opacity: 0.55; }
  .prop--headphones-bottom { left: 0; top: 868px; width: 180px; height: 254px; border-radius: 0 90px 90px 0; opacity: 0.55; }
  .prop--microphone { left: 712px; top: 820px; width: 224px; height: 82px; border-radius: 40px; transform: rotate(-8deg); }
  .prop--mic-arm { left: 880px; top: 690px; width: 330px; height: 26px; border-radius: 13px; transform-origin: left center; transform: rotate(42deg); }
  .host {
    position: absolute;
    left: 0; right: 0; top: 890px;
    text-align: center;
  }
  .host__mark {
    position: absolute;
    left: 568px; top: 8px;
    width: 64px; height: 64px;
    border-radius: 50%;
    background: var(--gold);
  }
  .host__with {
    position: absolute;
    left: 448px; top: 58px;
    font-family: "Yellowtail", cursive;
    font-size: 50px;
    color: var(--gold);
    line-height: 1;
    transform: rotate(-8deg);
  }
  .host__name {
    position: absolute;
    left: 0; right: 0; top: 96px;
    font-weight: 700;
    font-size: 66px;
    line-height: 1;
    letter-spacing: 0.5px;
  }
  .host__role {
    position: absolute;
    left: 0; right: 0; top: 180px;
    font-weight: 500;
    font-size: 19px;
    letter-spacing: 0.5px;
  }
  .host__show {
    position: absolute;
    left: 0; right: 0; top: 212px;
    font-weight: 400;
    font-size: 27px;
    letter-spacing: 0.5px;
  }
</style>
</head>
<body>
<main class="cover">
  <svg class="backdrop" width="1200" height="1200" viewBox="0 0 1200 1200" aria-hidden="true">
    <defs>
      <pattern id="grid" width="97" height="66" patternUnits="userSpaceOnUse" x="66" y="40">
        <path d="M97 0V66M0 66H97" fill="none" stroke="var(--grid)" stroke-width="1.2"/>
      </pattern>
    </defs>
    <rect width="1200" height="1200" fill="url(#grid)"/>
    <circle cx="230" cy="190" r="610" fill="none" stroke="var(--navy-ring)" stroke-width="70"/>
    <g class="dot-grid" fill="var(--gold)">
      <circle cx="6" cy="413" r="6"/><circle cx="26" cy="413" r="6"/>
      <circle cx="6" cy="435" r="6"/><circle cx="26" cy="435" r="6"/>
      <circle cx="6" cy="457" r="6"/><circle cx="26" cy="457" r="6"/>
      <circle cx="6" cy="479" r="6"/><circle cx="26" cy="479" r="6"/>
      <circle cx="6" cy="500" r="6"/><circle cx="26" cy="500" r="6"/>
    </g>
    <g class="triangle-stack">
      <polygon points="1111,506 1129,527 1093,527" fill="var(--white)"/>
      <polygon points="1111,531 1129,552 1093,552" fill="var(--gold)"/>
      <polygon points="1111,556 1129,577 1093,577" fill="var(--white)"/>
      <polygon points="1111,581 1129,602 1093,602" fill="var(--gold)"/>
      <polygon points="1111,606 1129,627 1093,627" fill="var(--white)"/>
    </g>
    <g class="chevrons" fill="none" stroke="var(--white)" stroke-width="3">
      <polyline points="1055,978 1031,1001 1055,1024"/>
      <polyline points="1077,978 1053,1001 1077,1024"/>
      <polyline points="1099,978 1075,1001 1099,1024"/>
      <polyline points="1121,978 1097,1001 1121,1024"/>
      <polyline points="1143,978 1119,1001 1143,1024"/>
    </g>
    <circle class="corner-disc" cx="1163" cy="1200" r="84" fill="var(--gold)"/>
  </svg>

  <div class="prop prop--headphones-top" role="img" aria-label="Studio headphones, blurred, top right"></div>
  <div class="prop prop--headphones-bottom" role="img" aria-label="Studio headphones, blurred, bottom left"></div>

  <h1 class="show-title show-title--top">Kettle Ridge</h1>
  <h1 class="show-title show-title--bottom">Kitchen Hour</h1>

  <div class="photo-frame"></div>
  <div class="guest-photo" role="img" aria-label="Guest headshot placeholder – drop photo here"></div>

  <div class="prop prop--mic-arm" role="img" aria-label="Microphone boom arm"></div>
  <div class="prop prop--microphone" role="img" aria-label="Podcast microphone"></div>

  <section class="host">
    <span class="host__mark"></span>
    <span class="host__with">With</span>
    <h2 class="host__name">MAYA OKAFOR</h2>
    <p class="host__role">PROFESSIONAL TITLE</p>
    <p class="host__show">KETTLE RIDGE KITCHEN HOUR</p>
  </section>
</main>
</body>
</html>
```